Exec Conference Design Concept

We need to refresh & update nonprofit association graphic design for annual meeting. The graphics will be used to promote the event primarily through digital communications & social media. Other materials we generate for this event are the agenda & billboard content. You can view the existing design at www.lutavorin.org under Events.

The target audience is primarily male, ages 35-60 in executive positions in C-Corps. The conference topics center on manufacturing regulations, marketing trends, and the economy. This conference has been around almost 30 years so we need something to invigorate potential registrants that will get their attention. It still needs to be professional and business-like.

In addition to a new design concept we would like to update the color palette. We’ve attached some mood boards with potential color & font suggestions. Our company logo is also attached and is the only design element tied to our branding that cannot be changed.

Designs should be energetic and sophisticated. Ideally, we would like the designs in Adobe Indesign or Photoshop. However, we can work with Illustrator.

Target Market(s)

Male business executives age 35-60.

Industry/Entity Type

Polystyrene manufacturing industry supply chain.

Other font styles liked:
• I usually prefer sans serif

Requirements
Must have
• Focus points to draw attention to higher level informational units. For example, some people will only read the headers and not detailed copy.
Nice to have
• Ways to insert bonus content that don’t over power other content. I like to see a good use of white space to enhance readability.

```html
<!DOCTYPE html>
<html lang="en">
<head>
<meta charset="utf-8">
<title>Lutavorin Expo 2026</title>
<link href="https://fonts.googleapis.com/css2?family=Lato:wght@400;700&family=Montserrat:wght@600;700&display=swap" rel="stylesheet">
<style>
  :root {
    --teal-dark: #1d5a5a;
    --teal-brand: #8fc3c0;
    --band: #e0f6f8;
    --ink: #1f2a2e;
    --muted: #3a4448;
    --white: #ffffff;
    --rule: #bcc4c6;
  }
  * { box-sizing: border-box; margin: 0; padding: 0; }
  html, body { width: 672px; height: 1200px; overflow: hidden; background: var(--white); }
  body { position: relative; font-family: "Lato", sans-serif; color: var(--ink); }

  .hero {
    position: absolute; left: 18px; top: 19px; width: 636px; height: 407px;
    border-radius: 0 30px 0 30px; overflow: hidden;
    background: linear-gradient(180deg, #6f9fcb 0%, #8db4d3 35%, #c9a3b0 62%, #3c3d48 78%, #23252c 100%);
    text-align: center; color: var(--white);
  }
  .brand {
    display: inline-flex; align-items: center; gap: 6px;
    font-family: "Lato", sans-serif; font-weight: 700; font-size: 16px; letter-spacing: .5px;
  }
  .brand-mark { width: 12px; height: 12px; background: var(--teal-brand); }
  .hero .brand { margin-top: 56px; color: var(--white); }
  .hero-title {
    font-family: "Montserrat", sans-serif; font-weight: 700; font-size: 24px; line-height: 31px;
    margin-top: 26px; text-shadow: 0 1px 4px rgba(0,0,0,.35);
  }
  .hero-lede {
    width: 420px; margin: 13px auto 0; font-size: 9.6px; line-height: 15.5px;
    text-shadow: 0 1px 3px rgba(0,0,0,.4);
  }
  .btn-register {
    display: inline-block; margin-top: 23px; width: 86px; height: 26px; line-height: 26px;
    background: var(--white); color: var(--teal-dark); font-size: 10px; text-decoration: none;
    border-radius: 8px 0 0 0;
  }

  .section-title {
    font-family: "Montserrat", sans-serif; font-weight: 600; font-size: 20px; color: var(--teal-dark);
  }
  .gain-title { position: absolute; top: 472px; width: 100%; text-align: center; }
  .gain-card { position: absolute; top: 517px; width: 171px; text-align: center; }
  .gain-photo { width: 171px; height: 168px; border-radius: 0 28px 0 28px; }
  .gain-label { margin-top: 8px; font-size: 12px; font-weight: 400; color: var(--ink); }
  .photo-a { background: linear-gradient(135deg, #2d4f6e, #cfc6b6 60%, #e9e3d8); }
  .photo-b { background: linear-gradient(135deg, #d8d2c6, #6e7f99 55%, #2e3f5c); }
  .photo-c { background: linear-gradient(135deg, #1f2f36, #3f6670 55%, #7dc4c4); }

  .attend {
    position: absolute; left: 18px; top: 756px; width: 636px; height: 211px;
    background: var(--band); border-radius: 6px;
  }
  .attend .section-title { position: absolute; left: 44px; top: 45px; }
  .attend-list { position: absolute; left: 44px; top: 88px; list-style: none; }
  .attend-list li { display: flex; align-items: center; gap: 10px; height: 21.7px; font-size: 8.5px; color: var(--muted); }
  .attend-photo {
    position: absolute; left: 328px; top: 40px; width: 261px; height: 135px;
    border-radius: 0 28px 0 28px;
    background: linear-gradient(180deg, #6f7a7a 0%, #c79a62 50%, #4a3a2c 100%);
  }

  .footer { position: absolute; top: 1022px; width: 100%; text-align: center; }
  .footer .brand { color: var(--teal-dark); }
  .footer-note { margin-top: 52px; font-size: 9px; color: var(--muted); }
  .event-meta { display: flex; justify-content: center; gap: 62px; margin-top: 18px; font-size: 10px; color: var(--muted); }
  .event-meta span { display: inline-flex; align-items: center; gap: 6px; }
  .footer-rule { width: 546px; height: 1px; background: var(--rule); margin: 16px auto 0; }
  .copyright { margin-top: 10px; font-size: 8.5px; color: var(--muted); }
</style>
</head>
<body>
  <header class="hero">
    <div class="hero-image" role="img" aria-label="Industrial power plant with smokestacks at sunset"></div>
    <div class="brand"><span class="brand-mark"></span>Lutavorin Expo 2026</div>
    <h1 class="hero-title">Lutavorin Expo 2026<br>Where Regulation, Communication &amp;<br>Economics Converge</h1>
    <p class="hero-lede">Lutavorin Expo brings together the leaders shaping the future of the EPS manufacturing industry. This high-impact conference delivers clear insight into regulation, strategic communication, and the economic forces influencing your business.</p>
    <a class="btn-register" href="#">Register Now</a>
  </header>

  <h2 class="section-title gain-title">What You’ll Gain</h2>
  <div class="gain-card" style="left:62px">
    <div class="gain-photo photo-a" role="img" aria-label="Professional reviewing documents at a laptop"></div>
    <p class="gain-label">Regulatory Clarity</p>
  </div>
  <div class="gain-card" style="left:250px">
    <div class="gain-photo photo-b" role="img" aria-label="Colleagues shaking hands in an office"></div>
    <p class="gain-label">Industry Communication</p>
  </div>
  <div class="gain-card" style="left:438px">
    <div class="gain-photo photo-c" role="img" aria-label="Analyst studying data screens"></div>
    <p class="gain-label">Economic Intelligence</p>
  </div>

  <section class="attend">
    <h2 class="section-title">Who Should Attend</h2>
    <ul class="attend-list">
      <li><svg width="10" height="10" viewBox="0 0 10 10"><circle cx="5" cy="5" r="5" fill="#4a5357"/><path d="M2.6 5h4.4M5.2 3.2 7 5 5.2 6.8" stroke="#fff" stroke-width="1" fill="none"/></svg>EPS manufacturers and suppliers</li>
      <li><svg width="10" height="10" viewBox="0 0 10 10"><circle cx="5" cy="5" r="5" fill="#4a5357"/><path d="M2.6 5h4.4M5.2 3.2 7 5 5.2 6.8" stroke="#fff" stroke-width="1" fill="none"/></svg>Company owners and executive leadership</li>
      <li><svg width="10" height="10" viewBox="0 0 10 10"><circle cx="5" cy="5" r="5" fill="#4a5357"/><path d="M2.6 5h4.4M5.2 3.2 7 5 5.2 6.8" stroke="#fff" stroke-width="1" fill="none"/></svg>Compliance, regulatory, and government affairs teams</li>
      <li><svg width="10" height="10" viewBox="0 0 10 10"><circle cx="5" cy="5" r="5" fill="#4a5357"/><path d="M2.6 5h4.4M5.2 3.2 7 5 5.2 6.8" stroke="#fff" stroke-width="1" fill="none"/></svg>Industry advocates and decision-makers</li>
    </ul>
    <div class="attend-photo" role="img" aria-label="Refinery towers silhouetted against a golden sunset"></div>
  </section>

  <footer class="footer">
    <div class="brand"><span class="brand-mark"></span>Lutavorin Expo 2026</div>
    <p class="footer-note">You are receiving this email because you are part of the Lutavorin Industry Alliance network.</p>
    <div class="event-meta">
      <span><svg width="11" height="13" viewBox="0 0 11 13"><path d="M5.5 0A4.5 4.5 0 0 0 1 4.5C1 8 5.5 12 5.5 12S10 8 10 4.5A4.5 4.5 0 0 0 5.5 0z" fill="#1d5a5a"/><circle cx="5.5" cy="4.5" r="1.7" fill="#fff"/></svg>City, State</span>
      <span><svg width="13" height="13" viewBox="0 0 13 13"><rect x="0.5" y="2" width="12" height="10.5" rx="1" fill="#1d5a5a"/><rect x="3" y="0" width="1.5" height="3" fill="#1d5a5a"/><rect x="8.5" y="0" width="1.5" height="3" fill="#1d5a5a"/><g fill="#fff"><rect x="2.5" y="5.5" width="2" height="1.6"/><rect x="5.5" y="5.5" width="2" height="1.6"/><rect x="8.5" y="5.5" width="2" height="1.6"/><rect x="2.5" y="8.5" width="2" height="1.6"/><rect x="5.5" y="8.5" width="2" height="1.6"/><rect x="8.5" y="8.5" width="2" height="1.6"/></g></svg>Month Day–Day, 2026</span>
    </div>
    <div class="footer-rule"></div>
    <p class="copyright">© 2026 Lutavorin Industry Alliance. All rights reserved.</p>
  </footer>
</body>
</html>
```